Brochure for Healthy Restaurant Concept

Please design a brochure for our meal prep menu . Include all items and all descriptions of the items . Include some photos. Please ensure you let us know what size paper your design will need to be printed on. Please make it a clean modern design, matching our logo and its ok to use other colors as well. We are open to designs. We dont want it to be too plain.

Include all items including the pre-built options, bundles, and custom meals on the brochure. I will include the old brochure to give you an example, don't copy items and prices from that particular brochure as they could be inaccurate for the "Pre-Built items and breakfast items now.

Industry/Entity Type

Restaurant

Requirements
Must have
• Logo, all menu items
Nice to have
• A QR code linking our website www.ploverbarn.example

```html
<!DOCTYPE html>
<html lang="en">
<head>
<meta charset="utf-8">
<title>Plover Barn – Meal Prep Brochure</title>
<link href="https://fonts.googleapis.com/css2?family=Bebas+Neue&family=Lato:wght@400;700;900&display=swap" rel="stylesheet">
<style>
  :root{
    --canvas:#e9e9e8;
    --paper:#e3e2df;
    --green:#7aab2a;
    --green-light:#9cc63f;
    --green-dark:#5d8a1c;
    --ink:#1f1f1f;
    --band:#232323;
    --white:#ffffff;
    --grey-text:#3a3a3a;
  }
  *{box-sizing:border-box;margin:0;padding:0}
  html,body{width:1200px;height:857px;overflow:hidden;background:var(--canvas)}
  body{position:relative;font-family:'Lato',sans-serif;color:var(--ink)}
  .page{position:absolute;top:32px;width:560px;height:792px;overflow:hidden;box-shadow:0 6px 24px rgba(0,0,0,.18)}
  .page--back{left:40px;background:var(--paper)}
  .page--front{left:600px}
  .layer{position:absolute;inset:0;width:100%;height:100%}
  .heading{font-family:'Bebas Neue',sans-serif;font-weight:400;letter-spacing:.5px;line-height:1}

  /* product grid */
  .product{position:absolute;width:140px}
  .product__photo{height:78px;border-radius:2px;background:linear-gradient(135deg,#b59a72,#6b5a45)}
  .product__photo--pasta{background:linear-gradient(135deg,#8a9a3e,#4f5a2a)}
  .product__photo--rice{background:linear-gradient(135deg,#e6e0d2,#8b7d68)}
  .product__label{display:flex;justify-content:space-between;margin-top:6px;font-family:'Bebas Neue',sans-serif;font-size:11px;letter-spacing:.3px;color:var(--grey-text)}
  .product__price{color:var(--green)}

  .app-promo{position:absolute;left:36px;top:440px;width:220px}
  .app-promo__title{font-size:30px;color:var(--ink)}
  .app-promo__text{margin-top:12px;font-size:13px;line-height:1.45;text-align:justify;color:var(--ink)}
  .store-badges{display:flex;gap:10px;margin-top:14px}
  .store-badge{width:76px;height:24px;border-radius:4px;background:var(--ink)}
  .store-badge--light{background:var(--white);border:1px solid #bbb}

  .phones{position:absolute;display:flex;gap:12px}
  .phone{width:78px;height:160px;border-radius:12px;background:#5a5a5a;padding:5px;box-shadow:0 4px 10px rgba(0,0,0,.3)}
  .phone__screen{width:100%;height:100%;border-radius:8px;background:linear-gradient(180deg,#3b3b3b,#a0512e)}
  .phone__screen--list{background:linear-gradient(180deg,#b44e2a 0 38%,#f4f4f2 38%)}
  .phone__screen--feed{background:linear-gradient(180deg,#f4f4f2 0 14%,#8a6a58 14% 55%,#b8572c 55%)}

  .footer-band{position:absolute;left:0;right:0;bottom:0;height:152px;background:var(--band)}
  .brand{position:absolute;display:flex;align-items:center;gap:6px}
  .brand__dot{width:10px;height:10px;border-radius:50%;background:var(--green)}
  .brand__name{font-family:'Lato',sans-serif;font-weight:900;font-size:22px;letter-spacing:1px}
  .brand__tag{position:absolute;top:28px;left:0;white-space:nowrap;font-weight:900;font-size:9px;letter-spacing:.4px;color:var(--green)}
  .brand--light .brand__name{color:var(--white)}
  .contact{position:absolute;left:270px;top:678px;font-size:14px;line-height:1.55;color:var(--white);font-style:normal}

  /* front */
  .hero-photo{position:absolute;inset:0;background:linear-gradient(160deg,#e7ebee 0 28%,#d8c9b0 40%,#c4773a 58%,#b9823c 72%,#8b8f86 100%)}
  .brand--front{right:30px;top:64px}
  .brand--front .brand__name{font-size:30px;color:var(--ink)}
  .brand--front .brand__tag{top:40px;font-size:12px}
  .courier-ring{position:absolute;left:34px;top:190px;width:226px;height:226px;border-radius:50%;background:var(--green);padding:10px}
  .courier-photo{width:100%;height:100%;border-radius:50%;background:linear-gradient(160deg,#c8ced2,#8f4658 60%,#2d3a5c)}
  .intro{position:absolute;left:296px;top:232px;width:234px}
  .intro__title{font-size:24px;color:var(--ink)}
  .intro__text{margin-top:8px;font-size:12px;line-height:1.38;color:var(--ink)}
  .tagline{position:absolute;left:30px;top:446px;width:252px;font-size:21px;line-height:1.08;color:var(--white)}
</style>
</head>
<body>

<section class="page page--back">
  <svg class="layer" viewBox="0 0 560 792" aria-hidden="true">
    <polygon points="0,210 180,580 560,350 560,792 0,792" fill="var(--green)"/>
    <polygon points="0,210 180,580 0,640" fill="var(--green-light)" opacity=".55"/>
    <polygon points="180,580 560,350 560,420" fill="var(--green-dark)" opacity=".35"/>
  </svg>

  <div class="product" style="left:58px;top:40px"><div class="product__photo" role="img" aria-label="Tray of sweet potato mash"></div><div class="product__label"><span>16oz Sweet Potato Mash</span><span class="product__price">$9.00</span></div></div>
  <div class="product" style="left:214px;top:52px"><div class="product__photo product__photo--rice" role="img" aria-label="Tray of mashed potato"></div><div class="product__label"><span>16oz Mashed Potato</span><span class="product__price">$9.00</span></div></div>
  <div class="product" style="left:370px;top:64px"><div class="product__photo" role="img" aria-label="Tray of roasted baby potatoes"></div><div class="product__label"><span>16oz Baby Potatoes</span><span class="product__price">$9.00</span></div></div>

  <div class="product" style="left:40px;top:170px"><div class="product__photo product__photo--rice" role="img" aria-label="Tray of brown rice"></div><div class="product__label"><span>16oz Brown Rice</span><span class="product__price">$7.00</span></div></div>
  <div class="product" style="left:196px;top:182px"><div class="product__photo product__photo--rice" role="img" aria-label="Tray of basmati rice"></div><div class="product__label"><span>16oz Basmati Rice</span><span class="product__price">$7.00</span></div></div>
  <div class="product" style="left:352px;top:194px"><div class="product__photo product__photo--rice" role="img" aria-label="Tray of quinoa"></div><div class="product__label"><span>16oz Quinoa</span><span class="product__price">$7.00</span></div></div>

  <div class="product" style="left:22px;top:300px"><div class="product__photo product__photo--pasta" role="img" aria-label="Tray of pesto pasta"></div><div class="product__label"><span>16oz Pesto Pasta</span><span class="product__price">$9.50</span></div></div>
  <div class="product" style="left:178px;top:312px"><div class="product__photo product__photo--pasta" role="img" aria-label="Tray of pesto pasta"></div><div class="product__label"><span>16oz Pesto Pasta</span><span class="product__price">$9.50</span></div></div>
  <div class="product" style="left:334px;top:324px"><div class="product__photo product__photo--pasta" role="img" aria-label="Tray of pesto pasta"></div><div class="product__label"><span>16oz Pesto Pasta</span></div></div>

  <div class="app-promo">
    <h2 class="heading app-promo__title">Order food<br>easily on our app</h2>
    <p class="app-promo__text">You can also download our mobile app from the play store and app store to choose your favorite meal from your favorite kitchen.</p>
    <div class="store-badges"><span class="store-badge"></span><span class="store-badge store-badge--light"></span></div>
  </div>

  <div class="phones" style="left:282px;top:448px">
    <div class="phone"><div class="phone__screen" role="img" aria-label="App welcome screen with meal photo"></div></div>
    <div class="phone"><div class="phone__screen phone__screen--feed" role="img" aria-label="App home screen with meal prep photos"></div></div>
    <div class="phone"><div class="phone__screen phone__screen--list" role="img" aria-label="App meal options screen"></div></div>
  </div>

  <div class="footer-band"></div>
  <div class="brand brand--light" style="left:36px;top:676px">
    <span class="brand__dot"></span><span class="brand__name">PLOVER BARN</span>
    <span class="brand__tag">HEALTHY KITCHEN | MEAL PREP</span>
  </div>
  <address class="contact">
    your address goes here<br>your address goes here<br>Tel 555 0142 0187<br>www.ploverbarn.example
  </address>
</section>

<section class="page page--front">
  <div class="hero-photo" role="img" aria-label="Pizza on parchment paper over a white wooden table"></div>
  <svg class="layer" viewBox="0 0 560 792" aria-hidden="true">
    <polygon points="560,300 560,792 250,792" fill="var(--green-light)" opacity=".75"/>
    <polygon points="0,420 420,792 0,792" fill="var(--green-dark)" opacity=".8"/>
    <polygon points="0,130 0,420 200,470" fill="#4a4a4a" opacity=".45"/>
  </svg>

  <div class="brand brand--front">
    <span class="brand__dot"></span><span class="brand__name">PLOVER BARN</span>
    <span class="brand__tag">HEALTHY KITCHEN | MEAL PREP</span>
  </div>

  <div class="courier-ring"><div class="courier-photo" role="img" aria-label="Delivery courier holding a paper bag and coffee"></div></div>

  <div class="intro">
    <h2 class="heading intro__title">Our Menu</h2>
    <p class="intro__text">Freshness, quality, nutrition profile, and flavour are just a few words to describe what goes into our menu choices here at Plover Barn Kitchen. We have a variety of items on our menu to ensure that when you stop by, you can be sure to find an item that fits your lifestyle. Everyone has different goals, and you'll see how our menu reflects that. The flavour of our dishes is what will surprise you the most. We have worked long and hard to provide the best quality, along with the best flavour profiles to have you leaving our store satisfied and planning to come back for dinner. Finally, a restaurant you can visit twice (or more) per day and not feel guilty!</p>
  </div>

  <h1 class="heading tagline">Plover Barn Kitchen delivery<br>your favourites, delivered<br>to your doorstep</h1>

  <div class="phones" style="left:292px;top:618px">
    <div class="phone"><div class="phone__screen" role="img" aria-label="App welcome screen with meal photo"></div></div>
    <div class="phone"><div class="phone__screen phone__screen--feed" role="img" aria-label="App home screen with meal prep photos"></div></div>
    <div class="phone"><div class="phone__screen phone__screen--list" role="img" aria-label="App meal options screen"></div></div>
  </div>
</section>

</body>
</html>
```